Hybrid Seed corn and Soybean Sales business needs a website.

We here at "KW Grain" feel that we need a website to show a very professional side to our customer base. Although no actual ordering will take place on this website, we would like to put Plot and field trail data on the website. Along with a brief page for each of our hybrids and a place for customers to sign up for a newsletter. The company we sell hybrids for is MolvanGrain.com... Im not sure how this process works as far as myself updating the information or having the data actually put on the website, but feel free to contact me if you need the information. I will attach the logo for the company, (KW Grain).

Target Market(s)

Farmers, "Producers", Corn and soybean production

Industry/Entity Type

Business

Coding

Coded - Design and coding required

Number of Pages Required

5+ page

Colors
f78f20
ffffff

Requirements
Nice to have
• Similar layout to http://www.molvangrain.com/
• And it would be nice to incorporate our story into the website
• http://www.molvangrain.com/our-story/molvan-today/

```html
<!DOCTYPE html>
<html lang="en">
<head>
<meta charset="utf-8">
<title>KW Grain – Hybrid Seed Corn &amp; Soybean</title>
<link href="https://fonts.googleapis.com/css2?family=Oswald:wght@600&family=Ubuntu:wght@400;500&display=swap" rel="stylesheet">
<style>
:root{
  --orange:#f78f20;
  --orange-dark:#e2791a;
  --green:#4e9a1b;
  --cream:#f8efe6;
  --page:#eeeeee;
  --text:#555555;
  --footer:#222222;
  --footer-bar:#1b1b1b;
  --footer-text:#d0d0d0;
  --white:#ffffff;
}
*{margin:0;padding:0;box-sizing:border-box}
html,body{width:929px;height:1200px;overflow:hidden}
body{position:relative;background:var(--page);font-family:'Ubuntu',sans-serif;color:var(--text)}

/* header */
.site-header{position:absolute;left:0;top:0;width:929px;height:69px;background:var(--orange);z-index:2}
.brand{position:absolute;left:72px;top:0;width:175px;height:80px;background:var(--cream);box-shadow:0 1px 3px rgba(0,0,0,.2);display:flex;align-items:center;justify-content:center;gap:7px}
.brand-dot{width:14px;height:14px;border-radius:50%;background:var(--green)}
.brand-name{font-weight:500;font-size:20px;color:var(--orange);letter-spacing:.5px}
.nav a{position:absolute;top:29px;font-size:10px;color:var(--white);text-decoration:none;text-transform:uppercase}
.nav .active-band{position:absolute;left:458px;top:0;width:54px;height:69px;background:var(--orange-dark)}

/* hero */
.hero{position:absolute;left:0;top:0;width:929px;height:430px;background:linear-gradient(180deg,#e0a040 0%,#d49030 35%,#a86a20 70%,#6e4414 100%)}
.hero-title{position:absolute;left:86px;top:222px;font-family:'Oswald',sans-serif;font-weight:600;font-size:40px;color:var(--white);letter-spacing:-.5px;text-transform:uppercase}
.hero-title span{color:var(--green)}
.hero-text{position:absolute;left:88px;top:279px;font-family:'Oswald',sans-serif;font-weight:600;font-size:11.3px;line-height:21.5px;color:var(--white);white-space:nowrap;letter-spacing:-.1px;text-shadow:0 1px 2px rgba(0,0,0,.6)}
.dots{position:absolute;left:446px;top:394px;display:flex;gap:5px}
.dots i{width:9px;height:9px;background:var(--white);display:block}
.dots i.on{background:var(--green)}

/* sections */
.heading{position:absolute;font-size:16px;font-weight:500;color:var(--orange);text-transform:uppercase}
.heading span{color:var(--green)}
.about-text{position:absolute;left:73px;top:495px;width:700px;font-size:8.8px;line-height:14.4px}
.media{position:absolute}
.video{left:72px;top:610px;width:235px;height:174px;background:linear-gradient(180deg,#3a2a1c 0%,#7a4a1a 55%,#d0801a 80%,#2a1a0c 100%)}
.video-bar{position:absolute;left:0;bottom:0;width:100%;height:18px;background:#1a1a1a;font-size:7px;color:#ddd;display:flex;align-items:center;padding-left:45px}
.video-bar .track{position:absolute;left:96px;top:7px;width:110px;height:4px;background:#444}
.video-bar .track b{display:block;width:38px;height:4px;background:#888}
.play{position:absolute;left:101px;top:56px;width:36px;height:36px;border-radius:50%;background:rgba(60,60,60,.7)}
.caption{position:absolute;left:73px;top:795px;font-size:7.2px;line-height:14.5px;text-transform:uppercase}
.seeds{left:352px;top:609px;width:245px;height:132px;background:linear-gradient(135deg,#c8306a,#e0607a 45%,#8a2048);border:1px solid #ccc}
.do-text{position:absolute;left:353px;top:748px;width:245px;font-size:8.8px;line-height:14.4px}
.more{position:absolute;left:354px;top:798px;font-size:8.8px;color:var(--orange)}

.event{position:absolute;left:642px;width:196px;height:64px}
.event .thumb{position:absolute;left:0;top:0;width:62px;height:55px;border:1px solid #ccc}
.event h4{position:absolute;left:73px;top:1px;font-size:7.2px;font-weight:500;color:#333;text-transform:uppercase;white-space:nowrap}
.event p{position:absolute;left:73px;top:14px;width:125px;font-size:7px;line-height:12.5px}
.event em{position:absolute;left:73px;top:42px;font-size:7px;color:var(--orange)}
.rule{position:absolute;left:644px;width:194px;height:1px;background:#999}

/* partners */
.partners{position:absolute;left:68px;top:862px;width:791px;height:60px;background:var(--white);border:1px solid #ddd}
.partners .arrow{position:absolute;top:22px;width:10px;height:16px;background:#e6e6e6;font-size:8px;color:#888;text-align:center;line-height:16px}
.partner{position:absolute;top:19px;display:flex;align-items:center;gap:6px;font-size:15px;font-weight:500;color:#333}
.partner i{width:14px;height:14px;display:block}

/* footer */
.site-footer{position:absolute;left:0;top:974px;width:929px;height:186px;background:var(--footer)}
.footer-bar{position:absolute;left:0;top:1160px;width:929px;height:40px;background:var(--footer-bar)}
.f-head{position:absolute;top:1005px;font-size:10px;font-weight:400;color:var(--white);text-transform:uppercase}
.f-list{position:absolute;top:1040px;list-style:none;font-size:10px;color:var(--footer-text)}
.f-list li{height:22.4px;padding-left:15px;position:relative}
.f-list li::before{content:"›";position:absolute;left:0;top:-1px}
.field{position:absolute;left:462px;width:156px;height:20px;background:var(--white);font-size:7.5px;color:#333;padding:5px 11px}
.submit{position:absolute;left:570px;top:1099px;width:48px;height:19px;background:#666;color:var(--white);font-size:8.5px;text-align:center;line-height:19px}
.contact-row{position:absolute;left:697px;display:flex;align-items:center;gap:12px;font-size:9.5px;color:var(--footer-text)}
.contact-row svg{width:13px;height:13px}
.copy{position:absolute;left:93px;top:1174px;font-size:8px;color:#888}
.social{position:absolute;left:724px;top:1170px;display:flex;gap:1px}
.social i{width:19px;height:19px;display:block}
</style>
</head>
<body>

<section class="hero" role="img" aria-label="Photo of a golden wheat field at sunset"></section>

<header class="site-header">
  <div class="brand"><span class="brand-dot"></span><span class="brand-name">KW GRAIN</span></div>
  <nav class="nav">
    <span class="active-band"></span>
    <a style="left:472px">Home</a>
    <a style="left:541px">About us</a>
    <a style="left:628px">Products</a>
    <a style="left:718px">Services</a>
    <a style="left:800px">Contact us</a>
  </nav>
</header>

<h1 class="hero-title">Welcome to <span>KW Grain</span></h1>
<p class="hero-text">Lorem ipsum dolor sit amet, consectetur adipiscing elit, sed do eiusmod tempor incididunt ut labore et dolore<br>magna aliqua. Ut enim trud exercitation ullamco laboris nisi ut aliquip ex ea commodo consequat. Duis aute irure<br>dolor in reprehenderit in voluptate velit esse cillum</p>
<div class="dots"><i class="on"></i><i></i><i></i></div>

<h2 class="heading" style="left:73px;top:467px">About <span>KW Grain</span></h2>
<p class="about-text">Lorem ipsum dolor sit amet, consectetur adipiscing elit, sed do eiusmod tempor incididunt ut labore et dolore magna aliqua. Ut enim ad minim veniam, quis nostrud exercitation ullamco laboris nisi ut aliquip ex ea commodo consequat. Duis aute irure dolor in reprehenderit in voluptate velit esse cillum dolore eu fugiat nulla pariatur. Excepteur sint occaecat cupidatat non proident, sunt in culpa qui officia deserunt mollit anim id est laborum</p>

<h2 class="heading" style="left:73px;top:576px">Our <span>Videos</span></h2>
<h2 class="heading" style="left:353px;top:576px">What <span>We Do</span></h2>
<h2 class="heading" style="left:641px;top:574px">Upcoming <span>Events</span></h2>

<div class="media video" role="img" aria-label="Video still of a sunset over a field">
  <span class="play"></span>
  <div class="video-bar">0:04 / 0:30<span class="track"><b></b></span></div>
</div>
<p class="caption">We sell hybrid seeds of corn &amp; soybean.<br>Cupidatat non proident, sunt in culpa qui officia</p>

<div class="media seeds" role="img" aria-label="Close-up photo of pink treated seed corn kernels"></div>
<p class="do-text">Lorem ipsum dolor sit amet, consectetur adipiscing elit, sed do eiusmod tempor incididunt ut labore et dolore magna aliqua. Ut enim ad minim veniam, quis nostrud</p>
<span class="more">[ READ MORE ]</span>

<article class="event" style="top:608px">
  <div class="thumb" role="img" aria-label="Photo of corn cobs" style="background:linear-gradient(135deg,#6a9ad0,#e8b020 50%,#6a8a2a)"></div>
  <h4>Various versions have evolved</h4>
  <p>Lorem ipsum dolor sit amet,elit, sed do eiusmod tempor ......</p>
  <em>Upcoming 16 May 2014</em>
</article>
<span class="rule" style="top:673px"></span>
<article class="event" style="top:684px">
  <div class="thumb" role="img" aria-label="Photo of green soybean pods" style="background:linear-gradient(135deg,#8ac040,#4e8a1a)"></div>
  <h4>Various versions have evolved</h4>
  <p>Lorem ipsum dolor sit amet,elit, sed do eiusmod tempor ......</p>
  <em>Upcoming 20 May 2014</em>
</article>
<span class="rule" style="top:749px"></span>
<article class="event" style="top:760px">
  <div class="thumb" role="img" aria-label="Close-up photo of a yellow corn cob" style="background:linear-gradient(135deg,#f0c020,#d89010)"></div>
  <h4>Various versions have evolved</h4>
  <p>Lorem ipsum dolor sit amet,elit, sed do eiusmod tempor ......</p>
  <em>Upcoming 24 May 2014</em>
</article>

<div class="partners">
  <span class="arrow" style="left:4px">‹</span>
  <div class="partner" style="left:66px"><i style="background:#d22"></i>Tarrow Agronomics</div>
  <div class="partner" style="left:382px"><i style="background:var(--orange)"></i>Molvan</div>
  <div class="partner" style="left:600px"><i style="background:var(--green)"></i>Fieldmark</div>
  <span class="arrow" style="right:4px">›</span>
</div>

<footer class="site-footer"></footer>
<div class="footer-bar"></div>

<h3 class="f-head" style="left:95px">Information</h3>
<ul class="f-list" style="left:97px"><li>Home</li><li>About us</li><li>Product</li><li>Services</li><li>Contact us</li></ul>

<h3 class="f-head" style="left:277px">Useful Links</h3>
<ul class="f-list" style="left:278px"><li>Focus corn hybrid</li><li>By Field Type</li><li>Refuge Plus</li><li>Stackline</li><li>Technology Tool</li></ul>

<h3 class="f-head" style="left:461px">News Letter Sign Up</h3>
<div class="field" style="top:1042px">Name</div>
<div class="field" style="top:1072px">Email ID</div>
<div class="submit">SUBMIT</div>

<h3 class="f-head" style="left:697px">Contact Us</h3>
<div class="contact-row" style="top:1037px">
  <svg viewBox="0 0 13 13"><rect x="1" y="2" width="11" height="10" fill="#999"/><rect x="3" y="4" width="7" height="3" fill="#222"/></svg>+000 555 0142</div>
<div class="contact-row" style="top:1059px">
  <svg viewBox="0 0 13 13"><path d="M2 1l3 0 1 3-2 1.5c1 2 2 3 3.5 3.5L9 7l3 1v3c-6 0-10-4-10-10z" fill="#999"/></svg>+000 555 0142</div>
<div class="contact-row" style="top:1082px">
  <svg viewBox="0 0 13 13"><rect x="0.5" y="2.5" width="12" height="8" fill="#999"/><path d="M0.5 2.5l6 5 6-5" fill="none" stroke="#222" stroke-width="1"/></svg>contact@kwgrain.net</div>

<p class="copy">Copyright © 2015 KW Grain.. All right reserved.</p>
<div class="social"><i style="background:#f7a81b"></i><i style="background:#3aa0d8"></i><i style="background:#3b5a98"></i><i style="background:#3a70c0"></i><i style="background:#2a8ab8"></i></div>

</body>
</html>
```